Book cover design for a collection of poetry - The Lanternfield

Book cover and back design need to be moody, nostalgic, reflective, ethereal. Melancholy and other worldly. Cover design should not be time specific to a period or place but if applicable should reflect British landscape. Book cover should be in tones of blue and must include the title and author (THE LANTERNFIELD BY CORBIN WHITLACE). We love the idea of rain, and looking out of a window. See attached designs. A world you are observing but not in.

Industry/Entity Type

Book Publisher

Font styles to use
Serif
Script

Colors
3176b5
3377b5
85acd3
eaf1f7
0792cd
33a6d7
86cae7
ecf7fb
86cfc6

Requirements
Must have
• The colour blue in it, must be melancholy and reflective.
Nice to have
• Rain in the cover.
Should not have
• Any bright colours.

```html
<!DOCTYPE html>
<html lang="en">
<head>
<meta charset="utf-8">
<title>The Lanternfield — Corbin Whitlace</title>
<link rel="stylesheet" href="https://fonts.googleapis.com/css2?family=Playfair+Display:ital,wght@0,400;1,400&family=Montserrat:wght@400&display=swap">
<style>
  :root {
    --page: #ffffff;
    --frame-dark: #0a0e16;
    --frame-edge: #121826;
    --night-top: #1f3b66;
    --night-mid: #2a4f80;
    --night-low: #33577f;
    --lamp-warm: #c8934a;
    --lamp-glow: #e6b86a;
    --ink-light: #f4f6f8;
  }
  * { margin: 0; padding: 0; box-sizing: border-box; }
  html, body {
    width: 1200px;
    height: 1000px;
    overflow: hidden;
    background: var(--page);
  }
  .canvas {
    position: relative;
    width: 1200px;
    height: 1000px;
  }
  .book-cover {
    position: absolute;
    left: 322px;
    top: 50px;
    width: 598px;
    height: 898px;
    background: linear-gradient(180deg, var(--frame-edge) 0%, var(--frame-dark) 100%);
    overflow: hidden;
  }
  .rain-scene {
    position: absolute;
    left: 0;
    top: 0;
    width: 458px;
    height: 755px;
    background:
      radial-gradient(ellipse 160px 120px at 62% 92%, rgba(230,184,106,0.85), rgba(230,184,106,0) 100%),
      radial-gradient(ellipse 280px 200px at 20% 80%, rgba(140,70,60,0.35), rgba(140,70,60,0) 100%),
      linear-gradient(180deg, var(--night-top) 0%, var(--night-mid) 45%, var(--night-low) 78%, var(--lamp-warm) 100%);
  }
  .window-bar {
    position: absolute;
    background: var(--frame-dark);
    box-shadow: 0 0 6px rgba(0,0,0,0.6);
  }
  .window-bar--mullion { left: 153px; top: 0; width: 25px; height: 755px; }
  .window-bar--transom { left: 0; top: 215px; width: 458px; height: 35px; }
  .window-bar--jamb { left: 458px; top: 0; width: 140px; height: 898px; background: linear-gradient(90deg, #0c111b, #05070c); }
  .window-bar--sill { left: 0; top: 755px; width: 458px; height: 143px; background: linear-gradient(180deg, #0e131d, #05070b); }
  .cover-title {
    position: absolute;
    left: -8px;
    top: 36px;
    width: 598px;
    text-align: center;
    color: var(--ink-light);
    font-family: "Playfair Display", serif;
    font-weight: 400;
  }
  .cover-title__article {
    display: block;
    font-style: italic;
    font-size: 48px;
    line-height: 1;
  }
  .cover-title__main {
    display: block;
    margin-top: 18px;
    font-size: 68px;
    line-height: 1;
    letter-spacing: 0;
  }
  .cover-author {
    position: absolute;
    left: 0;
    top: 818px;
    width: 598px;
    text-align: center;
    color: var(--ink-light);
    font-family: "Montserrat", sans-serif;
    font-size: 24px;
    letter-spacing: 0.5px;
  }
</style>
</head>
<body>
<main class="canvas">
  <section class="book-cover">
    <div class="rain-scene" role="img" aria-label="Soft painted night view through a rain-streaked window, deep blue above with warm light below"></div>
    <div class="window-bar window-bar--mullion"></div>
    <div class="window-bar window-bar--transom"></div>
    <div class="window-bar window-bar--jamb"></div>
    <div class="window-bar window-bar--sill"></div>
    <h1 class="cover-title">
      <span class="cover-title__article">The</span>
      <span class="cover-title__main">LANTERNFIELD</span>
    </h1>
    <p class="cover-author">BY CORBIN WHITLACE</p>
  </section>
</main>
</body>
</html>
```